sydney wedding photography business needs a business card design

we need a business card design for a sydney based wedding photography and videography business. our business name is :golden hour studio and film. our target clients are 24-35 yrs female. our style is candid, organic, natural, dynamic. we are a team of young photographers and videographers, and help brides to create memories that they will cherish for the rest of their lives. the logo will be provided. we want an elegant design that reflects our style, and also want to give a great impression to our clients that we are one of the best studios in sydney and our brand means quality and premium service.

Target Market(s)

bride to be, 24-35 years old, living in sydney and surrunding areas

Industry/Entity Type

Wedding Photography

Contact Information for Business Card

address: 57 tarrant street, glenmore nsw 2047
mobile: 0431872259
phone: (02) 9163 2408
info@tidewillowstudio.net.au
www.tidewillowstudio.net.au
facebook:tidewillowweddings
instagram:tidewillowweddings

Font styles to use
Serif
Sans Serif

Requirements
Nice to have
• maybe add my slogan"memories beyond eternity" if the layout looks good
Should not have
• no black color, not good idea for wedding biz card

```html
<!DOCTYPE html>
<html lang="en">
<head>
<meta charset="utf-8">
<title>Golden Hour Studio and Film – Business Card</title>
<link rel="stylesheet" href="https://fonts.googleapis.com/css2?family=Arimo:wght@400;600&display=swap">
<style>
  :root {
    --backdrop: #3a302b;
    --card: #f5efe4;
    --card-edge: #e2d6c2;
    --gold: #b5842a;
    --gold-soft: #a87a26;
    --text-main: #4a423b;
    --text-muted: #7d7368;
    --brand-back: #b5842a;
    --rule: #c9bba5;
  }
  * { box-sizing: border-box; margin: 0; padding: 0; }
  html, body {
    width: 1200px; height: 864px; overflow: hidden;
    background: var(--backdrop);
    font-family: "Arimo", Arial, sans-serif;
  }
  .canvas { position: relative; width: 1200px; height: 864px; }

  .card {
    position: absolute;
    width: 540px; height: 310px;
    background: var(--card);
    border: 1px solid var(--card-edge);
    box-shadow: 0 10px 28px rgba(0,0,0,.45);
  }

  /* back of card */
  .card-back { left: 70px; top: 80px; }
  .back-brand {
    position: absolute; left: 0; right: 0; top: 92px;
    color: var(--brand-back);
    font-size: 30px; font-weight: 600;
    letter-spacing: 1px;
    display: flex; align-items: center; justify-content: center; gap: 12px;
  }
  .back-brand .mark {
    width: 18px; height: 18px; border-radius: 50%;
    background: var(--brand-back);
  }
  .back-rule {
    position: absolute; left: 40px; right: 40px; top: 204px;
    height: 1px; background: linear-gradient(90deg, transparent, var(--rule) 30%, var(--rule) 70%, transparent);
  }
  .back-dot {
    position: absolute; left: 262px; top: 197px;
    width: 16px; height: 16px; border-radius: 50%;
    background: var(--text-muted); border: 3px solid var(--card);
  }
  .back-handle {
    position: absolute; left: 0; right: 0; top: 222px;
    text-align: center; color: var(--text-muted);
    font-size: 15px; letter-spacing: .5px;
  }

  /* front of card */
  .card-front { left: 600px; top: 440px; }
  .front-brand {
    position: absolute; left: 150px; right: 30px; top: 52px;
    color: var(--gold);
    font-size: 27px; font-weight: 600;
    text-align: center; line-height: 1.15;
  }
  .person {
    position: absolute; left: 40px; top: 156px; width: 170px;
    text-align: right;
  }
  .person-name { color: var(--gold-soft); font-size: 17px; }
  .person-role { color: var(--text-main); font-size: 15px; margin-top: 4px; }
  .person-address { color: var(--text-main); font-size: 12.5px; margin-top: 8px; line-height: 1.35; }
  .divider {
    position: absolute; left: 228px; top: 158px;
    width: 1px; height: 104px; background: var(--rule);
  }
  .contacts {
    position: absolute; left: 246px; top: 156px;
    list-style: none;
  }
  .contacts li {
    display: flex; align-items: center; gap: 10px;
    color: var(--text-main); font-size: 14px;
    height: 26px;
  }
  .contacts svg { width: 15px; height: 15px; fill: var(--gold); flex: none; }
  .contacts .globe-lines { stroke: var(--card); }
</style>
</head>
<body>
<div class="canvas">

  <section class="card card-back" aria-label="Card back">
    <div class="back-brand"><span class="mark"></span>golden hour studio and film</div>
    <div class="back-rule"></div>
    <div class="back-dot"></div>
    <p class="back-handle">tidewillowweddings</p>
  </section>

  <section class="card card-front" aria-label="Card front">
    <h1 class="front-brand">golden hour studio and film</h1>

    <div class="person">
      <p class="person-name">Liam Archer</p>
      <p class="person-role">President</p>
      <p class="person-address">57 tarrant street<br>glenmore nsw 2047</p>
    </div>

    <div class="divider"></div>

    <ul class="contacts">
      <li>
        <svg viewBox="0 0 16 16" aria-hidden="true"><path d="M1 5c0-2 3-3 7-3s7 1 7 3v1h-4V5H5v1H1z"/><path d="M3 8h10l1 6H2z"/></svg>
        (02) 9163 2408
      </li>
      <li>
        <svg viewBox="0 0 16 16" aria-hidden="true"><path d="M4 1h8v14H4zM5.5 2.5v9h5v-9z" fill-rule="evenodd"/></svg>
        0431 872 259
      </li>
      <li>
        <svg viewBox="0 0 16 16" aria-hidden="true"><path d="M1 3h14v10H1zM2 4l6 5 6-5z" fill-rule="evenodd"/></svg>
        info@tidewillowstudio.net.au
      </li>
      <li>
        <svg viewBox="0 0 16 16" aria-hidden="true"><circle cx="8" cy="8" r="7"/><path class="globe-lines" d="M1 8h14M8 1c3 3 3 11 0 14M8 1c-3 3-3 11 0 14" stroke-width="1" fill="none"/></svg>
        www.tidewillowstudio.net.au
      </li>
    </ul>
  </section>

</div>
</body>
</html>
```